Web Developer Needs a Business Card Design

I need a personal business card design that represents me as a web developer for potential employers. I would like the background to be a dark color on the front for contrast with my logo and name. The back will have all my information along with a smaller version of the logo. I want something with a modern look and feel, not too conservative. This will be used for potential employers and freelance work.

Industry/Entity Type

Business

Contact Information for Business Card

Front should have my logo and name. The back should have all my personal information which would include: name: Tom Varulek, phone: 570-614-3098, email: tomvarulek@quillbox.net, website url: www.tomvarulek.net, logo, web developer.

Font styles to use
Sans Serif

Requirements
Must have
• Must include my logo. The color palette base color will be the logo color.

```html
<!DOCTYPE html>
<html lang="en">
<head>
<meta charset="utf-8">
<title>Tom Varulek – Business Card</title>
<link rel="stylesheet" href="https://fonts.googleapis.com/css2?family=Open+Sans:wght@300;400;600;700&display=swap">
<style>
  :root {
    --teal: #5cc2ab;
    --teal-deep: #47b098;
    --ink: #0c0c0c;
    --paper: #ffffff;
    --text-dark: #1a1a1a;
    --backdrop: #e8e5e0;
  }
  * { box-sizing: border-box; margin: 0; padding: 0; }
  html, body {
    width: 1200px; height: 913px; overflow: hidden;
    background: var(--backdrop);
    font-family: "Open Sans", Arial, sans-serif;
  }
  .stage {
    position: relative; width: 1200px; height: 913px;
    display: flex; align-items: center; justify-content: center; gap: 60px;
  }
  .card {
    position: relative; width: 540px; height: 309px; overflow: hidden;
    box-shadow: 0 8px 24px rgba(0,0,0,.18);
  }

  /* Dark side */
  .card--front { background: var(--ink); }
  .accent-band {
    position: absolute; left: 40px; top: 0; width: 100px; height: 100%;
    background: linear-gradient(180deg, var(--teal) 0%, var(--teal-deep) 100%);
  }
  .info-band {
    position: absolute; left: 140px; top: 66px; width: 400px; height: 124px;
    background: var(--paper);
  }
  .brand-mark {
    position: absolute; left: 88px; top: 132px; width: 124px; height: 124px;
    border-radius: 50%; background: var(--ink);
    border: 7px solid var(--teal);
    display: flex; align-items: center; justify-content: center;
  }
  .brand-mark__name {
    color: var(--teal); font-weight: 600; font-size: 17px;
  }
  .contact {
    position: absolute; right: 22px; top: 76px; text-align: right;
    color: var(--text-dark);
  }
  .contact__name { font-size: 21px; font-weight: 700; letter-spacing: .5px; line-height: 1.1; }
  .contact__role { font-size: 12px; font-weight: 600; color: var(--teal); letter-spacing: 1px; margin-bottom: 6px; }
  .contact__line {
    font-size: 13px; line-height: 18px;
    display: flex; justify-content: flex-end; align-items: center; gap: 6px;
  }
  .contact__line svg { width: 11px; height: 11px; flex: none; }

  /* Light side */
  .card--back {
    background: var(--paper);
    display: flex; flex-direction: column; align-items: center;
  }
  .brand-mark--light {
    position: static; margin-top: 46px; width: 96px; height: 96px;
    background: var(--paper); border-width: 5px;
  }
  .brand-mark--light .brand-mark__name { font-size: 15px; }
  .back__name {
    margin-top: 34px; font-size: 30px; font-weight: 300; letter-spacing: 3px;
    color: var(--text-dark);
  }
  .back__role { margin-top: 8px; font-size: 15px; color: var(--text-dark); }
</style>
</head>
<body>
<main class="stage">
  <section class="card card--front">
    <div class="accent-band"></div>
    <div class="info-band"></div>
    <div class="contact">
      <p class="contact__name">TOM VARULEK</p>
      <p class="contact__role">WEB DEVELOPER</p>
      <p class="contact__line">570-614-3098
        <svg viewBox="0 0 24 24" fill="none" stroke="#5cc2ab" stroke-width="2.4"><path d="M5 3h4l2 5-2.5 1.5a11 11 0 0 0 6 6L16 13l5 2v4a2 2 0 0 1-2 2A16 16 0 0 1 3 5a2 2 0 0 1 2-2z"/></svg>
      </p>
      <p class="contact__line">tomvarulek@quillbox.net
        <svg viewBox="0 0 24 24" fill="none" stroke="#5cc2ab" stroke-width="2.4"><rect x="3" y="5" width="18" height="14"/><path d="M3 5l9 8 9-8"/></svg>
      </p>
      <p class="contact__line">www.tomvarulek.net
        <svg viewBox="0 0 24 24" fill="none" stroke="#5cc2ab" stroke-width="2.2"><circle cx="12" cy="12" r="9"/><path d="M3 12h18M12 3c3 3 3 15 0 18M12 3c-3 3-3 15 0 18"/></svg>
      </p>
    </div>
    <div class="brand-mark"><span class="brand-mark__name">Varulek</span></div>
  </section>

  <section class="card card--back">
    <div class="brand-mark brand-mark--light"><span class="brand-mark__name">Varulek</span></div>
    <p class="back__name">TOM VARULEK</p>
    <p class="back__role">Front-End Developer</p>
  </section>
</main>
</body>
</html>
```